Lawn care business card

I am looking for a quality designed personal business card to represent the quality and elegant nature of our company. We separate ourselves in our market by the aesthetic value of our work, so I am looking for marketing material that does the same. We target our marketing high end customers, and we try to avoid price shoppers. I am open to all design options, so long as they are in line with our companies values.

We are tend to go with a retro look on everything from our logo and print material, to our uniforms. We like to portray and "old fashion" set of core values, with a modern elegance. So a wild and crazy look is out of the question.

Things I'd like on the card:
1.) Logo
2.) Phone number: (816) 555-2931
3.) Website: Verdelynkc.com
4.) Email: robertfairley@verdelynkc.com
5.) My name: Robert Fairley
6.) Facebook link: facebook.com/VerdelynGardenandGrounds
7.) Instagram: http://instagram.com/verdelynkc

Attached is a copy of our logo.

Reason: More time is needed to gather conclusive feedback from the members of our marketing team.

```html
<!DOCTYPE html>
<html lang="en">
<head>
<meta charset="utf-8">
<title>Verdelyn Business Card</title>
<link rel="stylesheet" href="https://fonts.googleapis.com/css2?family=Lato:wght@400;700&display=swap">
<style>
  :root {
    --backdrop: #2b2b2b;
    --card: #fbfbfa;
    --accent: #e8540f;
    --accent-soft: #f08a4f;
    --ink: #1e1e1e;
    --ink-muted: #2c2c2c;
  }
  html, body {
    margin: 0;
    padding: 0;
    width: 1200px;
    height: 1116px;
    overflow: hidden;
    background: var(--backdrop);
    font-family: "Lato", sans-serif;
  }
  .business-card {
    position: absolute;
    left: 100px;
    top: 272px;
    width: 1000px;
    height: 571px;
    background: var(--card);
    box-shadow: 0 18px 40px rgba(0,0,0,0.45);
  }
  .card-frame {
    position: absolute;
    inset: 20px;
    border: 7px solid var(--accent);
  }
  .identity {
    position: absolute;
    left: 62px;
    top: 150px;
  }
  .identity-name {
    margin: 0;
    font-size: 36px;
    font-weight: 400;
    color: var(--accent);
    line-height: 1.1;
  }
  .identity-name .first-name { color: var(--accent-soft); }
  .identity-role {
    margin: 6px 0 0;
    font-size: 19px;
    font-weight: 700;
    letter-spacing: 0.5px;
    color: var(--ink);
  }
  .contact-list {
    position: absolute;
    left: 62px;
    bottom: 62px;
    margin: 0;
    padding: 0;
    list-style: none;
    font-size: 23px;
    font-weight: 700;
    color: var(--ink-muted);
    line-height: 44px;
  }
  .brand-lockup {
    position: absolute;
    right: 90px;
    top: 110px;
    display: flex;
    align-items: center;
    gap: 22px;
  }
  .brand-dot {
    width: 110px;
    height: 110px;
    flex: none;
  }
  .brand-name {
    font-size: 64px;
    font-weight: 700;
    color: var(--ink);
    letter-spacing: 1px;
  }
</style>
</head>
<body>
  <article class="business-card">
    <div class="card-frame"></div>

    <div class="brand-lockup">
      <svg class="brand-dot" viewBox="0 0 110 110" aria-hidden="true">
        <circle cx="55" cy="55" r="55" fill="var(--accent)"/>
      </svg>
      <span class="brand-name">Verdelyn</span>
    </div>

    <header class="identity">
      <h1 class="identity-name"><span class="first-name">Robert</span> Fairley</h1>
      <p class="identity-role">OWNER / FOUNDER</p>
    </header>

    <ul class="contact-list">
      <li>Tel: (816) 555-2931</li>
      <li>Email: robertfairley@verdelynkc.com</li>
      <li>instagram.com/verdelynkc</li>
      <li>facebook.com/VerdelynGardenandGrounds</li>
    </ul>
  </article>
</body>
</html>
```